Firm Stationery Design

I need a design for stationery, including: Stationery First Page, Stationery Second Sheet, Envelope, Mailing Label for Flat Envelopes, and Business Cards

```html
<!DOCTYPE html>
<html lang="en">
<head>
<meta charset="utf-8">
<title>Harlow Law LLC — Business Cards</title>
<link href="https://fonts.googleapis.com/css2?family=Arimo:wght@400;700&display=swap" rel="stylesheet">
<style>
  :root {
    --backdrop: #3d3d3d;
    --brand-orange: #fea001;
    --ink: #1b1b1b;
    --paper: #ffffff;
    --gold: #b8790a;
  }
  * { margin: 0; padding: 0; box-sizing: border-box; }
  html, body {
    width: 1200px; height: 803px; overflow: hidden;
    background: var(--backdrop);
    font-family: "Arimo", Arial, sans-serif;
  }
  .stage {
    position: relative; width: 1200px; height: 803px;
  }
  .card {
    position: absolute; top: 262px;
    width: 490px; height: 280px;
    border-radius: 18px;
  }
  .card-front {
    left: 80px;
    background: var(--brand-orange);
    padding: 58px 40px 30px 44px;
    color: var(--paper);
  }
  .card-back {
    left: 630px;
    background: var(--paper);
    display: flex; align-items: center; justify-content: center;
  }
  .firm-name {
    font-weight: 700; color: var(--ink);
    letter-spacing: 1px; line-height: 1.05;
    text-transform: uppercase;
  }
  .card-front .firm-name { font-size: 26px; }
  .card-back .firm-name { font-size: 40px; text-align: center; }
  .firm-name .suffix { display: block; letter-spacing: 8px; }
  .card-front .firm-name .suffix { font-size: 13px; margin-top: 4px; }
  .card-back .firm-name .suffix { font-size: 18px; margin-top: 8px; letter-spacing: 14px; }
  .holder { margin-top: 14px; }
  .holder-name { font-size: 19px; font-weight: 700; color: var(--ink); }
  .holder-title { font-size: 11px; margin-top: 2px; }
  .address { margin-top: 12px; font-size: 11px; line-height: 1.4; }
  .contacts { list-style: none; margin-top: 8px; font-size: 11px; line-height: 1.45; }
  .contacts li { display: flex; align-items: center; gap: 7px; }
  .contacts svg { width: 10px; height: 10px; flex: none; }
</style>
</head>
<body>
<main class="stage">
  <section class="card card-front">
    <div class="firm-name">Harlow<span class="suffix">Law LLC</span></div>
    <div class="holder">
      <div class="holder-name">Daniel Reyes</div>
      <div class="holder-title">President</div>
    </div>
    <div class="address">412 Alder Court<br>Fairview, Canada 20815</div>
    <ul class="contacts">
      <li><svg viewBox="0 0 10 10"><path d="M2 1l2 2-1 1.3c.6 1.2 1.4 2 2.7 2.7L7 6l2 2-1.3 1.5C4.5 9.3.7 5.5.5 2.3z" fill="var(--ink)"/></svg>555-210-4817</li>
      <li><svg viewBox="0 0 10 10"><rect x="2.5" y="0.5" width="5" height="9" rx="1" fill="none" stroke="var(--ink)"/></svg>555-390-6142</li>
      <li><svg viewBox="0 0 10 10"><rect x="0.5" y="2" width="9" height="6" fill="var(--ink)"/><path d="M0.5 2L5 5.5 9.5 2" stroke="var(--brand-orange)" fill="none"/></svg>info@harlowlaw.com</li>
      <li><svg viewBox="0 0 10 10"><circle cx="5" cy="5" r="4.5" fill="var(--ink)"/><path d="M.5 5h9M5 .5c-2 2.5-2 6.5 0 9M5 .5c2 2.5 2 6.5 0 9" stroke="var(--brand-orange)" stroke-width=".7" fill="none"/></svg>www.harlowlaw.com</li>
    </ul>
  </section>

  <section class="card card-back">
    <div class="firm-name">Harlow<span class="suffix">Law LLC</span></div>
  </section>
</main>
</body>
</html>
```